Large footwear retailer needs new powerpoint template

We are an Australian footwear retailer - Wombelle Kicks that needs a new powerpoint template. We want it to be fun and using our brand colours Teal and Black.
This will be used for multiple presentations so should include title slides, slides that allow us to high light our digital execution's, graphs, overviews and detail.
It can be bold and playful but also easy to use.
our website: https://www.wombellekicks.com.au/
Our Instagram: https://www.instagram.com/wombelle_trainers/

```html
<!DOCTYPE html>
<html lang="en">
<head>
<meta charset="utf-8">
<title>Wombelle Kicks – Presentation Template</title>
<link rel="stylesheet" href="https://fonts.googleapis.com/css2?family=Poppins:wght@400;600;700;800&family=Open+Sans:wght@400;600&display=swap">
<style>
:root{
  --teal:#1aa99c;
  --teal-dark:#0d7f76;
  --teal-pale:#d8f1ee;
  --ink:#111314;
  --grey:#6c7173;
  --bar-grey:#c9cccd;
  --page:#ececec;
  --white:#ffffff;
}
*{box-sizing:border-box;margin:0;padding:0}
html,body{width:1200px;height:4040px;overflow:hidden;background:var(--page)}
body{position:relative;font-family:"Open Sans",Arial,sans-serif;color:var(--ink)}
.slide{position:absolute;left:88px;width:1024px;height:576px;overflow:hidden;background:var(--white);border:1px solid #dcdcdc}
.s1{top:88px;background:var(--teal)}
.s2{top:740px}.s3{top:1392px}.s4{top:2044px}.s5{top:2696px}.s6{top:3348px}

.brand{position:absolute;display:flex;align-items:center;gap:8px;font-family:"Poppins",sans-serif;font-weight:800;color:var(--ink);letter-spacing:.5px}
.brand-dot{width:16px;height:16px;border-radius:50%;background:var(--teal);flex:none}
.slide .brand-top{left:34px;top:28px;font-size:20px}

.photo{position:absolute}
.title{position:absolute;font-family:"Poppins",sans-serif;font-weight:700;font-size:24px;text-transform:uppercase}
.lorem{font-size:11px;line-height:1.55;color:var(--grey)}

.footer{position:absolute;left:0;bottom:0;width:1024px;height:110px}
.footer svg{position:absolute;inset:0}
.footer-text{position:absolute;bottom:14px;left:34px;right:34px;display:flex;justify-content:space-between;font-size:9.5px;color:var(--white)}

/* slide 1 */
.s1 .scene-left{left:0;top:0;width:360px;height:576px;background:linear-gradient(135deg,#2b8f88,#0f5f59)}
.s1 .scene-right{right:0;top:0;width:360px;height:576px;background:linear-gradient(200deg,#3aa59c,#0d6b64)}
.s1 .hero-panel{position:absolute;left:250px;top:0;width:500px;height:576px;background:var(--white);border-radius:0 0 0 240px}
.s1 .hero-shoe{left:330px;top:60px;width:360px;height:300px;border-radius:50%;background:radial-gradient(circle,#2f6be0 0%,#1f4fb8 55%,#e6ecf7 70%,#fff 72%)}
.s1 .brand{left:390px;top:420px;font-size:38px}
.s1 .brand-dot{width:30px;height:30px}

/* slide 2 */
.s2 .side-band{position:absolute;right:0;top:0;width:110px;height:576px;background:var(--teal);display:flex;align-items:center;justify-content:center}
.s2 .side-band span{transform:rotate(90deg);white-space:nowrap;font-family:"Poppins",sans-serif;font-weight:700;font-size:20px;color:var(--white);letter-spacing:1px}
.s2 .feature-shoe{left:60px;top:170px;width:300px;height:220px;border-radius:20px;background:linear-gradient(135deg,#f6c430,#e49a10)}
.s2 .copy{position:absolute;left:420px;top:90px;width:440px;display:flex;flex-direction:column;gap:18px}

/* slide 3 */
.s3 .title,.s4 .title{right:34px;top:26px}
.s3 .chart{position:absolute;left:40px;top:80px;width:560px;height:360px}
.s3 .points{position:absolute;left:640px;top:90px;width:340px;display:flex;flex-direction:column;gap:30px}
.point{display:flex;gap:10px}
.point i{width:8px;height:8px;border-radius:50%;background:var(--teal);margin-top:6px;flex:none}
.point h3{font-family:"Poppins",sans-serif;font-size:14px;font-weight:600}

/* slide 4 */
.s4 .product{left:40px;top:110px;width:400px;height:300px;border-radius:20px;background:linear-gradient(135deg,#3b3e42,#111314)}
.s4 .detail{position:absolute;left:480px;top:75px;width:500px}
.label{font-family:"Poppins",sans-serif;font-weight:700;font-size:12px;color:var(--teal);margin:12px 0 4px}
.price{font-family:"Poppins",sans-serif;font-weight:700;font-size:20px;margin-bottom:6px}
.ticks{list-style:none;display:flex;flex-direction:column;gap:5px}
.ticks li{display:flex;gap:8px;align-items:center;font-size:11px;color:var(--grey)}
.ticks svg{flex:none}

/* slide 5 */
.s5 .title-box{position:absolute;right:0;top:20px;width:440px;height:60px;background:var(--teal);color:var(--white);font-family:"Poppins",sans-serif;font-weight:700;font-size:26px;display:flex;align-items:center;padding-left:44px}
.steps{position:absolute;left:30px;top:150px;display:flex;gap:6px}
.step{width:236px;height:236px;border-radius:50%;background:var(--teal);color:var(--white);text-align:center;padding:34px 30px 0}
.step b{display:block;font-family:"Poppins",sans-serif;font-size:60px;line-height:1}
.step h3{font-family:"Poppins",sans-serif;font-size:14px;font-weight:600;margin:8px 0 6px}
.step p{font-size:9.5px;line-height:1.5;opacity:.9}

/* slide 6 */
.s6 .shoe-left{left:-20px;top:0;width:230px;height:150px;border-radius:0 0 80px 0;background:linear-gradient(135deg,#1c2c5a,#2fb38f)}
.s6 .shoe-right{right:-20px;top:0;width:230px;height:150px;border-radius:0 0 0 80px;background:linear-gradient(135deg,#e23c8a,#f27db4)}
.thanks{position:absolute;left:0;width:1024px;top:150px;text-align:center;font-family:"Poppins",sans-serif;font-weight:700;font-size:52px;letter-spacing:18px;color:var(--teal)}
.s6 .brand{left:340px;top:240px;font-size:42px}
.s6 .brand-dot{width:32px;height:32px}
.s6 .footer{height:200px}
.contacts{position:absolute;left:60px;right:60px;bottom:60px;display:flex;justify-content:space-between}
.contact{display:flex;gap:12px;align-items:center;color:var(--white);width:260px}
.contact .ico{width:48px;height:48px;border-radius:50%;background:var(--teal-dark);display:flex;align-items:center;justify-content:center;flex:none}
.contact h4{font-family:"Poppins",sans-serif;font-size:13px}
.contact p{font-size:10px;line-height:1.4}
</style>
</head>
<body>

<!-- Title slide -->
<section class="slide s1">
  <div class="photo scene-left" role="img" aria-label="Store interior photo with teal overlay"></div>
  <div class="photo scene-right" role="img" aria-label="Lifestyle photo of a person in sneakers with teal overlay"></div>
  <div class="hero-panel"></div>
  <div class="photo hero-shoe" role="img" aria-label="Blue running shoes product photo"></div>
  <div class="brand"><span>WOMBELLE KICKS</span><span class="brand-dot"></span></div>
</section>

<!-- Digital executions -->
<section class="slide s2">
  <div class="brand brand-top"><span>WOMBELLE KICKS</span><span class="brand-dot"></span></div>
  <div class="photo feature-shoe" role="img" aria-label="Yellow sneakers product photo"></div>
  <div class="copy">
    <p class="lorem">Lorem ipsum dolor sit amet, consectetur adipiscing elit, sed do eiusmod tempor incididunt ut labore et dolore magna aliqua. Ut enim ad minim veniam, quis nostrud exercitation ullamco laboris nisi ut aliquip ex ea commodo consequat. Duis aute irure dolor in reprehenderit in voluptate velit esse cillum dolore eu fugiat nulla pariatur.</p>
    <p class="lorem">Excepteur sint occaecat cupidatat non proident, sunt in culpa qui officia deserunt mollit anim id est laborum. Sed ut perspiciatis unde omnis iste natus error sit voluptatem accusantium doloremque laudantium, totam rem aperiam eaque ipsa quae ab illo inventore veritatis.</p>
    <p class="lorem">Excepteur sint occaecat cupidatat non proident, sunt in culpa qui officia deserunt mollit anim id est laborum nulla pariatur.</p>
  </div>
  <div class="side-band"><span>HIGHLIGHT OUR DIGITAL EXECUTIONS</span></div>
</section>

<!-- Graphs -->
<section class="slide s3">
  <div class="brand brand-top"><span>WOMBELLE KICKS</span><span class="brand-dot"></span></div>
  <h2 class="title">Our Graphs</h2>
  <svg class="chart" viewBox="0 0 560 360" font-family="Open Sans, sans-serif" font-size="10" fill="#6c7173">
    <g stroke="#e6e8e8">
      <line x1="40" y1="20" x2="550" y2="20"/><line x1="40" y1="70" x2="550" y2="70"/>
      <line x1="40" y1="120" x2="550" y2="120"/><line x1="40" y1="170" x2="550" y2="170"/>
      <line x1="40" y1="220" x2="550" y2="220"/><line x1="40" y1="270" x2="550" y2="270"/>
      <line x1="40" y1="320" x2="550" y2="320" stroke="#bbb"/>
    </g>
    <g text-anchor="end">
      <text x="32" y="24">120</text><text x="32" y="74">100</text><text x="32" y="124">80</text>
      <text x="32" y="174">60</text><text x="32" y="224">40</text><text x="32" y="274">20</text><text x="32" y="324">0</text>
    </g>
    <g>
      <rect x="58" y="70" width="22" height="250" fill="var(--bar-grey)"/><rect x="84" y="95" width="22" height="225" fill="var(--teal)"/>
      <rect x="130" y="90" width="22" height="230" fill="var(--bar-grey)"/><rect x="156" y="108" width="22" height="212" fill="var(--teal)"/>
      <rect x="202" y="150" width="22" height="170" fill="var(--bar-grey)"/><rect x="228" y="195" width="22" height="125" fill="var(--teal)"/>
      <rect x="274" y="70" width="22" height="250" fill="var(--bar-grey)"/><rect x="300" y="80" width="22" height="240" fill="var(--teal)"/>
      <rect x="346" y="80" width="22" height="240" fill="var(--bar-grey)"/><rect x="372" y="100" width="22" height="220" fill="var(--teal)"/>
      <rect x="418" y="170" width="22" height="150" fill="var(--bar-grey)"/><rect x="444" y="182" width="22" height="138" fill="var(--teal)"/>
      <rect x="490" y="82" width="22" height="238" fill="var(--bar-grey)"/><rect x="516" y="170" width="22" height="150" fill="var(--teal)"/>
    </g>
    <g text-anchor="middle" font-size="8">
      <text x="69" y="64">100</text><text x="95" y="89">90</text><text x="141" y="84">92</text><text x="167" y="102">85</text>
      <text x="213" y="144">68</text><text x="239" y="189">50</text><text x="285" y="64">100</text><text x="311" y="74">96</text>
      <text x="357" y="74">96</text><text x="383" y="94">88</text><text x="429" y="164">60</text><text x="455" y="176">55</text>
      <text x="501" y="76">95</text><text x="527" y="164">60</text>
    </g>
    <g text-anchor="middle">
      <text x="82" y="340">Sun</text><text x="154" y="340">Mon</text><text x="226" y="340">Tue</text><text x="298" y="340">Wed</text>
      <text x="370" y="340">Thu</text><text x="442" y="340">Fri</text><text x="514" y="340">Sat</text>
    </g>
  </svg>
  <div class="points">
    <div class="point"><i></i><div><h3>Duis aute irure dolor</h3><p class="lorem">Lorem ipsum dolor sit amet, consectetur adipiscing elit, sed do eiusmod.</p></div></div>
    <div class="point"><i></i><div><h3>Duis aute irure dolor</h3><p class="lorem">Lorem ipsum dolor sit amet, consectetur adipiscing elit, sed do eiusmod.</p></div></div>
    <div class="point"><i></i><div><h3>Duis aute irure dolor</h3><p class="lorem">Lorem ipsum dolor sit amet, consectetur adipiscing elit, sed do eiusmod.</p></div></div>
    <div class="point"><i></i><div><h3>Duis aute irure dolor</h3><p class="lorem">Lorem ipsum dolor sit amet, consectetur adipiscing elit, sed do eiusmod.</p></div></div>
  </div>
  <div class="footer">
    <svg viewBox="0 0 1024 110" preserveAspectRatio="none"><path d="M0 55 C170 20 300 85 520 60 S860 25 1024 50 V110 H0Z" fill="var(--teal)"/></svg>
    <div class="footer-text"><span>© 2022 Company Name | All Rights Reserved | Terms and Conditions</span><span>PAGE 00 - 03</span></div>
  </div>
</section>

<!-- Overview and detail -->
<section class="slide s4">
  <div class="brand brand-top"><span>WOMBELLE KICKS</span><span class="brand-dot"></span></div>
  <h2 class="title">Overviews and Detail</h2>
  <div class="photo product" role="img" aria-label="Black knit sneakers product photo"></div>
  <div class="detail">
    <p class="label">OVERVIEW</p>
    <p class="lorem">Lorem ipsum dolor sit amet, consectetur adipiscing elit, sed do eiusmod tempor incididunt ut labore et dolore magna aliqua. Ut enim ad minim veniam, quis nostrud exercitation ullamco laboris nisi ut aliquip ex ea commodo consequat.</p>
    <p class="lorem" style="margin-top:10px">Duis aute irure dolor in reprehenderit in voluptate velit esse cillum dolore eu fugiat nulla pariatur. Excepteur sint occaecat cupidatat non proident, sunt in culpa qui officia deserunt mollit anim.</p>
    <p class="label">DETAILS</p>
    <p class="price">$25.00</p>
    <ul class="ticks">
      <li><svg width="12" height="12" viewBox="0 0 12 12"><circle cx="6" cy="6" r="6" fill="var(--teal)"/><path d="M3 6.2l2 2 4-4.2" stroke="#fff" stroke-width="1.5" fill="none"/></svg>Lorem ipsum dolor sit amet, consectetur adipiscing elit.</li>
      <li><svg width="12" height="12" viewBox="0 0 12 12"><circle cx="6" cy="6" r="6" fill="var(--teal)"/><path d="M3 6.2l2 2 4-4.2" stroke="#fff" stroke-width="1.5" fill="none"/></svg>Sed do eiusmod tempor incididunt ut labore et dolore.</li>
      <li><svg width="12" height="12" viewBox="0 0 12 12"><circle cx="6" cy="6" r="6" fill="var(--teal)"/><path d="M3 6.2l2 2 4-4.2" stroke="#fff" stroke-width="1.5" fill="none"/></svg>Ut enim ad minim veniam, quis nostrud exercitation.</li>
      <li><svg width="12" height="12" viewBox="0 0 12 12"><circle cx="6" cy="6" r="6" fill="var(--teal)"/><path d="M3 6.2l2 2 4-4.2" stroke="#fff" stroke-width="1.5" fill="none"/></svg>Laboris nisi ut aliquip ex ea commodo consequat.</li>
    </ul>
  </div>
  <div class="footer">
    <svg viewBox="0 0 1024 110" preserveAspectRatio="none"><path d="M0 55 C170 20 300 85 520 60 S860 25 1024 50 V110 H0Z" fill="var(--teal)"/></svg>
    <div class="footer-text"><span>© 2022 Company Name | All Rights Reserved | Terms and Conditions</span><span>PAGE 00 - 04</span></div>
  </div>
</section>

<!-- How to purchase -->
<section class="slide s5">
  <div class="brand brand-top"><span>WOMBELLE KICKS</span><span class="brand-dot"></span></div>
  <div class="title-box">HOW TO PURCHASE</div>
  <div class="steps">
    <div class="step"><b>1</b><h3>Duis aute irure dolor</h3><p>Lorem ipsum dolor sit amet, consectetur adipiscing elit, sed do eiusmod tempor.</p></div>
    <div class="step"><b>2</b><h3>Duis aute irure dolor</h3><p>Lorem ipsum dolor sit amet, consectetur adipiscing elit, sed do eiusmod tempor.</p></div>
    <div class="step"><b>3</b><h3>Duis aute irure dolor</h3><p>Lorem ipsum dolor sit amet, consectetur adipiscing elit, sed do eiusmod tempor.</p></div>
    <div class="step"><b>4</b><h3>Duis aute irure dolor</h3><p>Lorem ipsum dolor sit amet, consectetur adipiscing elit, sed do eiusmod tempor.</p></div>
  </div>
  <div class="footer">
    <svg viewBox="0 0 1024 110" preserveAspectRatio="none"><path d="M0 55 C170 20 300 85 520 60 S860 25 1024 50 V110 H0Z" fill="var(--teal)"/></svg>
    <div class="footer-text"><span>© 2022 Company Name | All Rights Reserved | Terms and Conditions</span><span>PAGE 00 - 05</span></div>
  </div>
</section>

<!-- Thank you -->
<section class="slide s6">
  <div class="photo shoe-left" role="img" aria-label="Navy and green sneakers product photo"></div>
  <div class="photo shoe-right" role="img" aria-label="Pink sneakers product photo"></div>
  <h2 class="thanks">THANK YOU</h2>
  <div class="brand"><span>WOMBELLE KICKS</span><span class="brand-dot"></span></div>
  <div class="footer">
    <svg viewBox="0 0 1024 200" preserveAspectRatio="none"><path d="M0 60 C200 20 330 100 540 70 S870 20 1024 55 V200 H0Z" fill="var(--teal)"/></svg>
    <div class="contacts">
      <div class="contact">
        <span class="ico"><svg width="20" height="20" viewBox="0 0 24 24"><path d="M12 2a7 7 0 0 0-7 7c0 5 7 13 7 13s7-8 7-13a7 7 0 0 0-7-7zm0 9.5A2.5 2.5 0 1 1 12 6.5a2.5 2.5 0 0 1 0 5z" fill="#fff"/></svg></span>
        <div><h4>Address :</h4><p>21 Lorem Street, Anytown<br>VIC 3000 Australia</p></div>
      </div>
      <div class="contact">
        <span class="ico"><svg width="20" height="20" viewBox="0 0 24 24"><path d="M6.6 10.8a15 15 0 0 0 6.6 6.6l2.2-2.2a1 1 0 0 1 1-.25 11.4 11.4 0 0 0 3.6.57 1 1 0 0 1 1 1V20a1 1 0 0 1-1 1A17 17 0 0 1 3 4a1 1 0 0 1 1-1h3.5a1 1 0 0 1 1 1c0 1.25.2 2.45.57 3.57a1 1 0 0 1-.25 1z" fill="#fff"/></svg></span>
        <div><h4>Phone :</h4><p>+1 555 555 5555</p></div>
      </div>
      <div class="contact">
        <span class="ico"><svg width="20" height="20" viewBox="0 0 24 24"><rect x="3" y="5" width="18" height="14" rx="2" fill="#fff"/><path d="M3.5 6l8.5 7 8.5-7" stroke="var(--teal-dark)" stroke-width="1.6" fill="none"/></svg></span>
        <div><h4>Email :</h4><p>hello@wombellekicks.com.au</p></div>
      </div>
    </div>
    <div class="footer-text"><span>© 2022 Company Name | All Rights Reserved | Terms and Conditions</span><span>PAGE 00 - 06</span></div>
  </div>
</section>

</body>
</html>
```